Buch-/E-Book-Cover für Beziehungsratgeber
Zielgruppe
Wir verlegen Bücher, meistens Ratgeber
Aufgabenstellung
Das Design soll hohes Niveau (Verlagsniveau) haben und sich von den ganzen Billigvarianten abheben, die man so auf 'Quobbo' und co so findet. Ein simples Pix-Vault-Bild mit plakativem Text darüber würde ich als solche Billigvariante ansehen.
Da ich vom Design her noch keine klare Vorstellung habe, bin ich für verschiedene Vorschläge dankbar!
Ich benötige ein Buchcover für das EBook, das Taschenbuch und das Hardcover, incl. Mockup. Von der Gestaltung bin ich mir noch unsicher und von daher für Vorschläge offen.
Über das Buch:
Titel: Herzenswerkstatt
Untertitel: Der Weg zum gemeinsamen Morgen
Autor: Lukas Brandauer
Es ist ein Ratgeber für Beziehungen. Der Schwerpunkt ist die christliche orientierte Ehe, beschränkt sich aber nicht darauf. Auch wenn immer wieder biblische Zitate vorkommen, möchte ich keine religiösen Symbole auf dem Buch, weil es kein religiöses Lehrbuch ist.
Die Buchbeschreibung für die Rückseite lade ich als extra Datei hoch.
Ich stelle mir etwas vor, was man mit Herzenswerkstatt verbindet. Es kann auch gerne stilistisch sein, modern gehalten, aber nicht kalt. Es wäre schön, wenn es irgendwie die Liebe/Intimität einer tiefen Beziehung widerspiegelt. Am Besten kommt das Gefühl auf: „wie schön, das möchte ich auch“

```html
<!DOCTYPE html>
<html lang="de">
<head>
<meta charset="utf-8">
<title>Herzenswerkstatt – Buchcover</title>
<link rel="stylesheet" href="https://fonts.googleapis.com/css2?family=Poppins:wght@300;700&family=Montserrat:wght@700&display=swap">
<style>
  :root {
    --page-bg: #f3f2ef;
    --cover-bg: #f6f6f4;
    --band-beige: #e7e6df;
    --band-light: #eeeeea;
    --title-red: #a72a3a;
    --label-grey: #8a8a86;
    --sky-haze: #e4e0d2;
    --hill-amber: #c9a57a;
    --golden-light: #f0d2a4;
    --skin-peach: #e9bc98;
    --coat-taupe: #8c7665;
    --field-olive: #6f7048;
    --field-dark: #4f5233;
  }
  * { margin: 0; padding: 0; box-sizing: border-box; }
  html, body {
    width: 1175px;
    height: 1200px;
    overflow: hidden;
    background: var(--page-bg);
  }
  .cover {
    position: absolute;
    left: 187px;
    top: 50px;
    width: 800px;
    height: 1100px;
    background: var(--cover-bg);
    box-shadow: 0 6px 24px rgba(0,0,0,0.12);
    overflow: hidden;
  }
  .genre-band {
    position: absolute;
    left: 0; right: 0;
    top: 23px;
    height: 62px;
    background: var(--band-beige);
    display: flex;
    align-items: center;
    justify-content: center;
  }
  .genre {
    font-family: "Montserrat", sans-serif;
    font-weight: 700;
    font-size: 28px;
    letter-spacing: 0.36em;
    color: var(--label-grey);
    padding-left: 0.36em;
  }
  .title {
    position: absolute;
    left: 0; right: 0;
    top: 136px;
    text-align: center;
    font-family: "Poppins", sans-serif;
    font-weight: 700;
    font-size: 52px;
    letter-spacing: 0.1em;
    color: var(--title-red);
    padding-left: 0.1em;
  }
  .subtitle {
    position: absolute;
    left: 0; right: 0;
    top: 244px;
    text-align: center;
    font-family: "Poppins", sans-serif;
    font-weight: 300;
    font-size: 40px;
    line-height: 60px;
    letter-spacing: 0.09em;
    color: var(--title-red);
    padding-left: 0.09em;
  }
  .cover-photo {
    position: absolute;
    left: 0; right: 0;
    top: 416px;
    height: 548px;
    background:
      radial-gradient(ellipse 22% 34% at 4% 30%, rgba(140,118,101,0.85) 0%, rgba(140,118,101,0) 100%),
      radial-gradient(ellipse 26% 46% at 100% 58%, rgba(140,118,101,0.9) 0%, rgba(140,118,101,0) 100%),
      radial-gradient(ellipse 34% 22% at 46% 66%, rgba(233,188,152,0.85) 0%, rgba(233,188,152,0) 100%),
      radial-gradient(ellipse 55% 40% at 58% 48%, rgba(240,210,164,0.95) 0%, rgba(240,210,164,0) 100%),
      radial-gradient(ellipse 70% 14% at 40% 20%, rgba(201,165,122,0.7) 0%, rgba(201,165,122,0) 100%),
      linear-gradient(180deg, var(--sky-haze) 0%, #dcc9a8 28%, #d6b88e 50%, #a99a6c 72%, var(--field-olive) 88%, var(--field-dark) 100%);
  }
  .footer-light {
    position: absolute;
    left: 0; right: 0;
    top: 994px;
    height: 12px;
    background: var(--band-light);
  }
  .author-band {
    position: absolute;
    left: 0; right: 0;
    top: 1006px;
    height: 64px;
    background: var(--band-beige);
    display: flex;
    align-items: center;
    justify-content: center;
  }
  .author {
    font-family: "Montserrat", sans-serif;
    font-weight: 700;
    font-size: 29px;
    letter-spacing: 0.44em;
    color: var(--label-grey);
    padding-left: 0.44em;
  }
</style>
</head>
<body>
  <main class="cover">
    <div class="genre-band"><span class="genre">SACHBUCH</span></div>
    <h1 class="title">HERZENSWERKSTATT</h1>
    <p class="subtitle">DER WEG ZUM<br>GEMEINSAMEN MORGEN</p>
    <div class="cover-photo" role="img" aria-label="Foto: zwei Hände in Mantelärmeln, die sich zärtlich mit den kleinen Fingern berühren, vor unscharfer herbstlicher Landschaft im warmen goldenen Gegenlicht"></div>
    <div class="footer-light"></div>
    <div class="author-band"><span class="author">LUKAS BRANDAUER</span></div>
  </main>
</body>
</html>
```